Lanternfield Drinks business cards

We need a business card design for our new logo. The company is modern, progressive, professional, yet approachable. The key products are ready to drink bottles and cans of coffee based beverages.
These cards will be a critical part of the first impression made by our sales organization, business development team, and all external facing personnel.
Card can be a vertical or horizontal orientation.

Target Market(s)

Customers, suppliers, business partners

Industry/Entity Type

Business

Contact Information for Business Card

Business cards should feature Company Name and Logo.

Font styles to use
Serif

Colors

Designer to choose colors to be used in the design.

Requirements
Must have
• Strong readability of Name, phone #, mobile number and email address.
• Job title, website url, Street Address, and other details can be secondary level readability.
Nice to have
• High impact, simplistic quality design.
• Ok to utilize the 'H in the box' separate from the company name

```html
<!DOCTYPE html>
<html lang="en">
<head>
<meta charset="utf-8">
<title>Lanternfield Drinks – Business Cards</title>
<link rel="stylesheet" href="https://fonts.googleapis.com/css2?family=Crimson+Text:ital,wght@0,400;0,700;1,400&display=swap">
<style>
  :root {
    --backdrop: #b9b9b9;
    --orange-top: #e2862f;
    --orange-bottom: #c3502b;
    --brand-red: #cf4a26;
    --amber: #e0892f;
    --ink: #222222;
    --ink-soft: #333333;
    --card-white: #f6f6f6;
    --stripe-dark: #1c1c1c;
  }
  * { box-sizing: border-box; margin: 0; padding: 0; }
  html, body {
    width: 1200px; height: 576px; overflow: hidden;
    background: var(--backdrop);
    font-family: "Crimson Text", Georgia, serif;
  }
  .canvas { position: relative; width: 1200px; height: 576px; }

  .card {
    position: absolute; top: 138px; height: 294px;
    border-radius: 14px; overflow: hidden;
    box-shadow: 0 3px 8px rgba(0,0,0,0.25);
  }

  /* Front */
  .card-front {
    left: 82px; width: 484px;
    background: linear-gradient(180deg, var(--orange-top) 0%, var(--orange-bottom) 100%);
    color: #fff;
  }
  .front-mark {
    position: absolute; left: 203px; top: 78px; width: 77px; height: 77px;
    border: 4px solid #fff;
  }
  .front-name {
    position: absolute; left: 0; right: 0; top: 162px; text-align: center;
    font-weight: 700; color: #fff;
  }
  .front-name .name-main { display: block; font-size: 33px; letter-spacing: 1px; line-height: 1; }
  .front-name .name-sub {
    display: flex; align-items: center; justify-content: center; gap: 8px;
    font-size: 13px; letter-spacing: 2px; margin-top: 6px;
  }
  .front-name .rule { width: 70px; height: 2px; background: #fff; }

  /* Back */
  .card-back { left: 602px; width: 481px; background: var(--card-white); color: var(--ink); }
  .back-mark {
    position: absolute; left: 30px; top: 40px; width: 72px; height: 72px;
    border: 4px solid var(--brand-red);
  }
  .back-name { position: absolute; left: 116px; top: 52px; width: 276px; color: var(--brand-red); font-weight: 700; }
  .back-name .name-main { display: block; font-size: 32px; letter-spacing: 0.5px; line-height: 1; text-align: center; }
  .back-name .name-sub {
    display: flex; align-items: center; gap: 8px; font-size: 13px; letter-spacing: 2px; margin-top: 4px;
  }
  .back-name .rule { flex: 1; height: 2px; background: var(--brand-red); }

  .person { position: absolute; left: 30px; top: 204px; }
  .person-name { font-size: 19px; font-weight: 700; color: var(--brand-red); line-height: 1.1; }
  .person-title { font-size: 12.5px; font-style: italic; color: var(--ink-soft); }

  .contact { position: absolute; left: 268px; top: 152px; font-size: 13.5px; line-height: 17px; color: var(--ink); }
  .contact-row { display: flex; align-items: center; gap: 8px; }
  .contact-row svg { width: 12px; height: 12px; fill: var(--brand-red); flex: none; }
  .address { margin-top: 6px; }

  .bottom-bands { position: absolute; left: 0; bottom: 0; width: 481px; height: 40px; }
  .website {
    position: absolute; left: 266px; top: 262px; font-size: 13.5px; color: #fff; letter-spacing: 0.3px;
  }
</style>
</head>
<body>
<main class="canvas">

  <section class="card card-front" aria-label="Card front">
    <div class="front-mark"></div>
    <div class="front-name">
      <span class="name-main">LANTERNFIELD</span>
      <span class="name-sub"><span class="rule"></span>DRINKS CO<span class="rule"></span></span>
    </div>
  </section>

  <section class="card card-back" aria-label="Card back">
    <div class="back-mark"></div>
    <div class="back-name">
      <span class="name-main">LANTERNFIELD</span>
      <span class="name-sub"><span class="rule"></span>DRINKS CO<span class="rule"></span></span>
    </div>

    <div class="person">
      <p class="person-name">Mara Ellison</p>
      <p class="person-title">Managing Director</p>
    </div>

    <div class="contact">
      <p class="contact-row">
        <svg viewBox="0 0 24 24" aria-hidden="true"><path d="M3 8c0-3 4-5 9-5s9 2 9 5v2h-5V8H8v2H3z M6 12h12l2 9H4z"/></svg>
        312.480.2195
      </p>
      <p class="contact-row">
        <svg viewBox="0 0 24 24" aria-hidden="true"><path d="M7 1h10a2 2 0 0 1 2 2v18a2 2 0 0 1-2 2H7a2 2 0 0 1-2-2V3a2 2 0 0 1 2-2zm0 3v14h10V4z"/></svg>
        312.907.4418
      </p>
      <p class="contact-row">
        <svg viewBox="0 0 24 24" aria-hidden="true"><path d="M2 5h20v14H2z M3 6l9 7 9-7" stroke="#fff" stroke-width="1.5"/></svg>
        mara@lanternfielddrinks.com
      </p>
      <p class="address">87 Orchard Row,<br>Millbrook, US 123456</p>
    </div>

    <svg class="bottom-bands" viewBox="0 0 481 40" aria-hidden="true">
      <rect x="0" y="25" width="200" height="10" fill="var(--amber)"/>
      <polygon points="200,25 218,25 210,40 192,40" fill="var(--stripe-dark)"/>
      <polygon points="228,0 481,0 481,40 212,40" fill="var(--brand-red)"/>
    </svg>
    <p class="website">www.lanternfielddrinks.com</p>
  </section>

</main>
</body>
</html>
```